Redesign and move to Wordpress for corvandel.com

Our website needs a redesign and at the same time we are moving it to Wordpress. Please help us with a new digital professional look and feel.

We are an Australian Software Engineering company specialising in advanced software development using in A.I., PLatform Engineering, Integration and Cloud. See the current corvandel.com for more information about us.

```html
<!DOCTYPE html>
<html lang="en">
<head>
<meta charset="utf-8">
<title>Corvandel — Reliable Smart Software Engineering</title>
<link rel="stylesheet" href="https://fonts.googleapis.com/css2?family=Poppins:wght@400;500;600;700;800&family=Roboto:wght@400;500;700&display=swap">
<style>
:root{
  --black:#000000;
  --teal:#4fc6bb;
  --teal-bright:#3ac2b4;
  --blue:#1a5fa6;
  --blue-dark:#165a9e;
  --ink:#222222;
  --white:#ffffff;
  --grey-line:#d7d7d7;
  --footer-line:#444;
}
*{box-sizing:border-box;margin:0;padding:0}
html,body{width:1200px;height:3530px;overflow:hidden}
body{position:relative;background:var(--white);font-family:"Roboto",sans-serif;color:var(--ink)}
.abs{position:absolute}
.shapes{position:absolute;left:0;top:0}
/* header */
.brand{left:148px;top:22px;display:flex;align-items:center;gap:12px;color:var(--white);font-family:"Poppins",sans-serif;font-size:30px;font-weight:400;letter-spacing:1px}
.brand-mark{width:38px;height:38px;border:3px solid var(--white)}
.nav{left:605px;top:28px;display:flex;gap:34px;font-family:"Poppins",sans-serif;font-weight:600;font-size:16px;color:var(--white)}
.nav .active{color:var(--teal)}
.nav svg{margin-top:3px}
.hero-art{left:560px;top:60px;width:640px;height:470px;background:radial-gradient(ellipse at 60% 40%,#1d5fa8 0%,#0c2e5e 45%,#000 80%)}
.hero-title{left:148px;top:214px;font-family:"Poppins",sans-serif;font-weight:800;font-size:39px;line-height:48px;color:var(--white)}
.btn-outline{display:inline-block;font-family:"Roboto",sans-serif;font-weight:700;font-size:15px;padding:0 20px;line-height:42px;border:3px solid}
.hero-btn{left:148px;top:370px;color:var(--teal);border-color:var(--teal)}
.slide-dot{width:42px;height:42px;border-radius:50%;background:var(--white);display:flex;align-items:center;justify-content:center}
/* welcome */
.welcome-kicker{left:145px;top:678px;font-family:"Poppins",sans-serif;font-size:19px;color:var(--teal)}
.welcome-title{left:145px;top:706px;font-family:"Poppins",sans-serif;font-weight:800;font-size:40px;color:var(--blue)}
.welcome-text{left:145px;top:762px;width:407px;font-family:"Poppins",sans-serif;font-size:16px;line-height:24px;text-align:justify}
.welcome-btn{left:145px;top:945px;color:var(--blue);border-color:var(--blue);padding:0 26px}
.photo-main{left:655px;top:685px;width:328px;height:328px;border-radius:50%;background:linear-gradient(135deg,#3c4a5c,#8a96a6 55%,#2b3440)}
.photo-small{left:859px;top:861px;width:164px;height:164px;border-radius:50%;border:6px solid var(--white);background:linear-gradient(135deg,#5a6777,#b8c0c8)}
.clients{left:144px;top:1063px;display:flex;gap:12px}
.client{width:220px;height:134px;border:2px solid var(--grey-line);display:flex;align-items:center;justify-content:center;font-family:"Poppins",sans-serif;font-weight:700;font-size:28px;color:#333;gap:10px;background:var(--white)}
.client .dot{width:18px;height:18px;background:#333}
/* services */
.services-title{left:0;width:1200px;top:1380px;text-align:center;font-family:"Poppins",sans-serif;font-weight:800;font-size:40px;color:var(--white)}
.service{width:275px;color:var(--white)}
.service h3{font-family:"Poppins",sans-serif;font-weight:700;font-size:17px;line-height:24px;margin-top:10px}
.service p{font-size:14px;line-height:20px;text-align:justify;margin-top:4px}
/* news */
.news-title{left:0;width:1200px;top:2050px;text-align:center;font-family:"Poppins",sans-serif;font-weight:800;font-size:40px;color:#1e1e1e}
.card{top:2123px;width:295px;height:387px;background:var(--blue-dark);color:var(--white)}
.card-img{width:295px;height:168px;border-bottom-left-radius:180px 100px}
.card h3{font-family:"Poppins",sans-serif;font-weight:700;font-size:22px;text-align:center;margin-top:40px}
.card p{font-family:"Poppins",sans-serif;font-size:15px;line-height:20px;padding:0 30px;margin-top:12px;text-align:justify}
.card .go{position:absolute;right:25px;bottom:22px;width:30px;height:30px;border:2px solid var(--white);border-radius:50%;display:flex;align-items:center;justify-content:center}
/* promo */
.promo-box{left:205px;top:2651px;width:850px;height:386px;background:var(--teal);border-top-right-radius:190px;border-bottom-left-radius:160px}
.promo-photo{left:142px;top:2598px;width:480px;height:386px;background:linear-gradient(135deg,#8c9aa8,#cfd6dd 50%,#4c5c70);border-bottom-right-radius:190px}
.promo-title{left:652px;top:2728px;width:340px;font-family:"Poppins",sans-serif;font-weight:700;font-size:28px;line-height:36px;color:var(--white)}
.promo-field{left:649px;top:2888px;width:372px;height:58px;border-radius:29px;background:var(--white);display:flex;align-items:center;justify-content:space-between;padding:0 30px;font-family:"Poppins",sans-serif;font-size:15px;color:#666}
/* footer */
.f-head{font-family:"Poppins",sans-serif;font-weight:600;font-size:19px;line-height:28px;color:var(--white)}
.f-field{left:175px;top:3290px;width:271px;height:40px;border:1px solid #bbb;display:flex;align-items:center;justify-content:space-between;padding:0 16px;color:var(--white);font-size:13px}
.social{left:177px;top:3352px;display:flex;gap:6px}
.social span{width:26px;height:26px;border-radius:50%;background:#444}
.contact-row{display:flex;gap:22px;color:var(--white);font-size:12px;line-height:17px}
.contact-row b{font-size:15px;font-weight:700;display:block;margin-bottom:4px}
.links{display:grid;grid-template-columns:134px 150px;row-gap:14px;color:var(--white);font-size:15px;font-weight:500}
.links li{list-style:none}
.links li::before{content:"»";color:var(--teal);margin-right:14px}
.f-rule{left:171px;top:3455px;width:858px;height:1px;background:var(--footer-line)}
.copyright{left:0;width:1200px;top:3478px;text-align:center;color:var(--white);font-size:14px}
</style>
</head>
<body>

<svg class="shapes" width="1200" height="3530" aria-hidden="true">
  <rect x="0" y="0" width="1200" height="600" fill="#000"/>
  <path d="M0 1162 C90 1240 210 1318 380 1322 L1200 1322 L1200 2178 C1160 2050 1090 1962 1000 1959 L0 1959 Z" fill="#4fc6bb"/>
  <path d="M0 3160 L700 3160 C950 3150 1150 3060 1200 2993 L1200 3530 L0 3530 Z" fill="#000"/>
</svg>

<div class="abs hero-art" role="img" aria-label="Glowing blue circuit board traces"></div>
<svg class="shapes" width="1200" height="600" aria-hidden="true"><path d="M0 440 C120 540 240 596 380 600 L0 600 Z" fill="#fff"/></svg>

<header>
  <div class="abs brand"><span class="brand-mark"></span>corvandel</div>
  <nav class="abs nav">
    <span class="active">Home</span><span>Services</span><span>Contact</span><span>About</span><span>Blog</span>
    <svg width="16" height="16" viewBox="0 0 16 16"><circle cx="6.5" cy="6.5" r="5" fill="none" stroke="#fff" stroke-width="2.2"/><path d="M10 10l4.5 4.5" stroke="#fff" stroke-width="2.4"/></svg>
  </nav>
</header>

<section class="hero">
  <h1 class="abs hero-title">RELIABLE<br>SMART SOFTWARE<br>ENGINEERING</h1>
  <a class="abs btn-outline hero-btn">Read More</a>
  <div class="abs slide-dot" style="left:555px;top:512px"><svg width="12" height="14"><path d="M8 2L3 7l5 5" fill="none" stroke="#000" stroke-width="2"/></svg></div>
  <div class="abs slide-dot" style="left:603px;top:512px"><svg width="12" height="14"><path d="M4 2l5 5-5 5" fill="none" stroke="#000" stroke-width="2"/></svg></div>
</section>

<section class="welcome">
  <p class="abs welcome-kicker">WELCOME TO</p>
  <h2 class="abs welcome-title">CORVANDEL</h2>
  <p class="abs welcome-text">At Corvandel, we craft bespoke software solutions that are not available on the market. By building organizations market-leading products, process automation, legacy system enablement, or advanced intelligent systems, we empower our customers to achieve a competitive edge in their industry.</p>
  <a class="abs btn-outline welcome-btn">Read More</a>
  <div class="abs photo-main" role="img" aria-label="Two colleagues smiling while working at a laptop"></div>
  <div class="abs photo-small" role="img" aria-label="Team discussing work at a desk"></div>
  <div class="abs clients">
    <div class="client"><span>Brelton</span></div>
    <div class="client"><span class="dot"></span><span>Quillmark</span></div>
    <div class="client"><span>Tarrowin</span></div>
    <div class="client" style="font-weight:400;font-size:24px"><span>Marlowgate</span></div>
  </div>
</section>

<section class="services">
  <h2 class="abs services-title">SERVICES</h2>
  <svg class="shapes" width="1200" height="3530" aria-hidden="true" fill="none" stroke="#fff" stroke-width="2">
    <g transform="translate(166 1466)"><circle cx="28" cy="28" r="12"/><rect x="10" y="10" width="36" height="36"/><path d="M28 0v10M28 46v10M0 28h10M46 28h10"/></g>
    <g transform="translate(476 1466)"><circle cx="28" cy="28" r="9"/><circle cx="8" cy="8" r="6"/><circle cx="48" cy="8" r="6"/><circle cx="8" cy="48" r="6"/><circle cx="48" cy="48" r="6"/><path d="M13 13l8 8M43 13l-8 8M13 43l8-8M43 43l-8-8"/></g>
    <g transform="translate(783 1466)"><circle cx="44" cy="18" r="14"/><path d="M38 18l5 5 8-9M2 40h14l14 8h16l14-10v8L44 58H16L2 52z"/></g>
    <g transform="translate(166 1671)"><circle cx="28" cy="28" r="27"/><rect x="18" y="14" width="22" height="28"/><path d="M23 22h12M23 28h12M23 34h12"/></g>
    <g transform="translate(476 1671)"><circle cx="20" cy="20" r="12"/><circle cx="20" cy="20" r="5"/><circle cx="40" cy="40" r="14"/><circle cx="40" cy="40" r="6"/></g>
    <g transform="translate(783 1671)"><path d="M10 20v22l10 14h16l8-14V14M18 20V4M26 20V2M34 20V4M10 20l6-2"/><rect x="16" y="30" width="18" height="14"/></g>
  </svg>
  <div class="abs service" style="left:163px;top:1526px"><h3>ENTERPRISE Systems Integration</h3><p>Automate your business processes internally or externally to improve data quality and process efficiency</p></div>
  <div class="abs service" style="left:473px;top:1526px"><h3>Microservices</h3><p>Leverage Microservices Architecture enable deployment, dynamically scalable service performance, team productivity and more</p></div>
  <div class="abs service" style="left:782px;top:1526px"><h3>PLatform engineering</h3><p>For organisations looking to manage the security and cost risks around cloud infrastructure management for applications</p></div>
  <div class="abs service" style="left:163px;top:1732px"><h3>Conversational AI</h3><p>Enabling legacy systems with conversational user interfaces, or simply building intelligent natural language based services</p></div>
  <div class="abs service" style="left:473px;top:1732px"><h3>iPaaS</h3><p>Integration Platform as a Service brings the power of cloud based services to traditional integration. This is reliable enterprise systems</p></div>
  <div class="abs service" style="left:782px;top:1732px"><h3>Assistants / AI Agents</h3><p>The future of business AI are autonomous agents that specialise in your business data and processes.intelligence and insight along the way</p></div>
</section>

<section class="news">
  <h2 class="abs news-title">NEWS &amp; ARTICLES</h2>
  <svg class="abs" style="left:58px;top:2308px" width="16" height="24" aria-hidden="true"><path d="M12 2L3 12l9 10" fill="none" stroke="#1a5fa6" stroke-width="2.5"/></svg>
  <svg class="abs" style="left:1120px;top:2308px" width="16" height="24" aria-hidden="true"><path d="M4 2l9 10-9 10" fill="none" stroke="#1a5fa6" stroke-width="2.5"/></svg>
  <article class="abs card" style="left:144px">
    <div class="card-img" role="img" aria-label="Miniature workers repairing a circuit board" style="background:linear-gradient(135deg,#6a7f94,#c9b89a 50%,#3a4d62)"></div>
    <h3>INDUSTRY RESEARCH</h3>
    <p>(Halvorsen Research) Large language models (LLMs) have various tasks, but prompt engineering remains a challenge.</p>
    <span class="go"><svg width="14" height="14"><path d="M2 7h9M7 3l4 4-4 4" fill="none" stroke="#fff" stroke-width="2"/></svg></span>
  </article>
  <article class="abs card" style="left:453px">
    <div class="card-img" role="img" aria-label="Close-up of a green circuit board" style="background:linear-gradient(135deg,#0f3a2c,#2f7a5c 50%,#0a2219)"></div>
    <h3>RUNTIME &amp; CLOUD</h3>
    <p style="text-align:center">(Halvorsen Learning) Learn about the improvements coming in this beta release. ML toolkits, new compilers and more..</p>
    <span class="go"><svg width="14" height="14"><path d="M2 7h9M7 3l4 4-4 4" fill="none" stroke="#fff" stroke-width="2"/></svg></span>
  </article>
  <article class="abs card" style="left:760px">
    <div class="card-img" role="img" aria-label="Hand working on teal lit electronics" style="background:linear-gradient(135deg,#0c3a44,#1f8a94 55%,#04181c)"></div>
    <h3>INDUSTRY RESEARCH</h3>
    <p>(Halvorsen Research) Large language models (LLMs) have various tasks, but prompt engineering remains a challenge.</p>
    <span class="go"><svg width="14" height="14"><path d="M2 7h9M7 3l4 4-4 4" fill="none" stroke="#fff" stroke-width="2"/></svg></span>
  </article>
</section>

<section class="promo">
  <div class="abs promo-box"></div>
  <div class="abs promo-photo" role="img" aria-label="Two businessmen shaking hands and smiling"></div>
  <h2 class="abs promo-title">Australia's Largest health charity implements Corvandel API Msg Bus</h2>
  <div class="abs promo-field"><span>Email address</span><svg width="16" height="16"><path d="M1 8L15 1 11 15 8 9z" fill="#1a5fa6"/></svg></div>
</section>

<footer>
  <h4 class="abs f-head" style="left:175px;top:3216px">SUBSCRIBE TO<br>OUR NEWSLETTER</h4>
  <div class="abs f-field"><span>Email address</span><svg width="14" height="14"><path d="M1 7L13 1 10 13 7 8z" fill="#fff"/></svg></div>
  <div class="abs social"><span></span><span style="background:#fff"></span><span></span></div>

  <h4 class="abs f-head" style="left:488px;top:3216px">CONTACT INFO</h4>
  <div class="abs contact-row" style="left:490px;top:3275px">
    <svg width="14" height="18"><path d="M7 1a6 6 0 0 1 6 6c0 4-6 10-6 10S1 11 1 7a6 6 0 0 1 6-6z" fill="#4fc6bb"/><circle cx="7" cy="7" r="2.2" fill="#000"/></svg>
    <span>Level 9, 48 Wattlebrook Street<br>Carlton, VIC , 3053</span>
  </div>
  <div class="abs contact-row" style="left:488px;top:3330px">
    <svg width="20" height="14"><rect x="1" y="1" width="18" height="12" fill="#4fc6bb"/><path d="M1 1l9 7 9-7" fill="none" stroke="#000" stroke-width="1.5"/></svg>
    <span><b>Email</b>hello@corvandel.com</span>
  </div>
  <div class="abs contact-row" style="left:488px;top:3387px">
    <svg width="18" height="18"><path d="M3 1l4 1 1 4-2 2c1 2 3 4 5 5l2-2 4 1 1 4-2 2C8 18 0 10 1 3z" fill="#4fc6bb"/></svg>
    <span><b>Phone</b>1800 555 019</span>
  </div>

  <h4 class="abs f-head" style="left:734px;top:3216px">QUICK LINKS</h4>
  <ul class="abs links" style="left:734px;top:3274px">
    <li>Home</li><li>Terms and Condition</li>
    <li>About</li><li>Privacy policy</li>
    <li>Services</li><li>Help</li>
    <li>Contact</li><li>Support</li>
  </ul>
  <div class="abs f-rule"></div>
  <p class="abs copyright">© Copyrights 2025 | All Rights Reserved</p>
</footer>

</body>
</html>
```